Multi-Line Insurance PPC Landing Page - Conversion optimized.

We have a PPC landing page used for the general population to get an insurance quote through an agent's site.

We'd like to improve the page for PPC traffic, make it more conversion friendly.

Site should be a single long page.

We will dynamically change the form and headlines on the page depending on what insurance "line" is being called. ie, Lift, Auto, Home, Business.

The enclosed AI file has all of the raw elements we need. We're looking to enhance the design and conversion ability.

Target Market(s)

General public needed insurance services.

Industry/Entity Type

Insurance Broker

Number of Pages Required

1 page

Font styles to use
Sans Serif

Requirements
Must have
• Form, agent picture, name, address.

```html
<!DOCTYPE html>
<html lang="en">
<head>
<meta charset="utf-8">
<title>Insurance Agent – Get a Quote</title>
<link href="https://fonts.googleapis.com/css2?family=Open+Sans:wght@400;600;700&display=swap" rel="stylesheet">
<style>
:root{
  --blue:#1f5fa8;
  --blue-dark:#164a86;
  --navy:#0f3566;
  --green:#2f8a1e;
  --green-dark:#226b14;
  --ink:#333;
  --muted:#777;
  --line:#dcdcdc;
  --soft:#efefef;
  --white:#fff;
}
*{box-sizing:border-box;margin:0;padding:0}
html,body{width:1200px;height:2184px;overflow:hidden}
body{font-family:"Open Sans",Arial,sans-serif;color:var(--ink);background:var(--white);font-size:14px}
.btn{display:inline-block;background:var(--green);color:var(--white);font-weight:700;text-transform:uppercase;border-radius:2px}

.site-header{height:88px;display:flex;justify-content:space-between;align-items:center;padding:0 100px}
.brand{font-size:32px;font-weight:700;color:var(--blue)}
.call{display:flex;align-items:center;gap:10px}
.call small{display:block;font-size:12px;color:var(--muted)}
.call strong{font-size:20px;color:var(--blue)}

.hero{position:relative;height:512px;background:linear-gradient(180deg,#4a5560 0%,#8a959c 45%,#5b646b 100%)}
.hero-photo{position:absolute;inset:0}
.hero-nav{position:absolute;top:240px;width:28px;height:44px;background:rgba(255,255,255,.85);display:flex;align-items:center;justify-content:center}
.hero-nav.prev{left:0}.hero-nav.next{right:0}
.hero-copy{position:absolute;left:140px;top:210px}
.hero-title{background:rgba(30,30,30,.85);color:var(--white);font-size:38px;font-weight:700;padding:14px 24px}
.hero-copy .btn{margin-top:22px;font-size:20px;padding:14px 26px}

.lines{position:relative;margin-top:-52px;display:flex;justify-content:center;gap:28px;padding:0 116px}
.line-card{width:220px;background:var(--white);box-shadow:0 2px 8px rgba(0,0,0,.25);text-align:center;padding:0 16px 16px;position:relative}
.line-icon{width:100px;height:100px;border-radius:50%;background:var(--blue);border:5px solid var(--white);box-shadow:0 0 0 1px var(--line);margin:-52px auto 8px;display:flex;align-items:center;justify-content:center}
.line-card h3{font-size:24px;margin-bottom:6px}
.line-card p{font-size:12px;line-height:1.35;color:#555;margin-bottom:12px}
.line-card .btn{font-size:12px;padding:6px 14px}

.quote{display:flex;gap:20px;margin:56px 120px 0;height:440px}
.agent{width:380px;background:var(--soft);text-align:center;padding-top:24px}
.agent-photo{width:180px;height:180px;border-radius:50%;border:6px solid var(--blue);margin:0 auto 16px;background:linear-gradient(160deg,#c9ccd0,#5a6470)}
.agent h4{font-size:24px}
.agent .tel{display:flex;justify-content:center;align-items:center;gap:8px;font-size:18px;font-weight:600;margin:10px 0 24px}
.agent address{font-style:normal;font-size:16px;line-height:1.5}
.quote-form{flex:1;background:var(--soft);padding:20px 26px}
.quote-form h2{font-size:24px;color:var(--blue);font-weight:700;padding-bottom:12px;border-bottom:1px solid var(--line);margin-bottom:12px}
.quote-form h2 span{color:var(--ink)}
.fields{display:grid;grid-template-columns:1fr 1fr;column-gap:30px;row-gap:12px}
.field label{display:block;font-size:13px;margin-bottom:4px}
.input{height:28px;background:var(--white);border:1px solid var(--line);font-size:12px;color:#999;padding:5px 8px}
.triple{display:flex;gap:6px}.triple .input{flex:1}
.quote-form .btn{margin-top:16px;font-size:15px;padding:7px 30px;border:0}

.about{text-align:center;padding:36px 200px 0;height:184px}
.section-title{font-size:32px;font-weight:700;color:var(--blue)}
.section-title span{color:var(--ink)}
.about p{margin-top:14px;font-size:15px;line-height:1.6;color:#555}

.reviews{background:var(--soft);height:380px;padding-top:30px}
.reviews-head{display:flex;justify-content:center;align-items:center;gap:30px}
.reviews-list{display:flex;gap:40px;padding:34px 140px 0}
.review{flex:1}
.bubble{background:var(--white);border-radius:8px;padding:24px 30px;font-size:14px;line-height:1.5;color:#555;position:relative}
.who{display:flex;align-items:center;gap:40px;margin:16px 0 0 30px}
.who .pic{width:76px;height:76px;border-radius:50%;border:4px solid var(--white);background:linear-gradient(160deg,#b8bcc2,#6a727c)}
.who span{color:var(--green);font-weight:600}

.partners{height:200px;padding-top:30px;text-align:center}
.partners .section-title{display:inline-block;border:1px solid var(--line);padding:6px 30px}
.partner-row{display:flex;justify-content:center;align-items:center;gap:54px;margin-top:36px}
.partner{display:flex;align-items:center;gap:8px;font-size:26px;font-weight:700;color:#222}
.partner i{width:16px;height:16px;background:var(--blue);display:block}

.disclaimer{background:var(--blue);color:var(--white);text-align:center;height:116px;padding:20px 140px}
.disclaimer h5{font-size:15px;margin-bottom:6px}
.disclaimer p{font-size:12px;line-height:1.5;opacity:.9}
.site-footer{background:var(--navy);color:var(--white);height:64px;display:flex;justify-content:space-between;align-items:center;padding:0 100px;font-size:13px}
.site-footer .brand{color:var(--white);font-size:24px;font-weight:600}
</style>
</head>
<body>

<header class="site-header">
  <div class="brand">Insurance Agent</div>
  <div class="call">
    <svg width="30" height="30" viewBox="0 0 24 24"><path fill="#1f5fa8" d="M6.6 10.8a15 15 0 006.6 6.6l2.2-2.2c.3-.3.7-.4 1-.2 1.1.4 2.3.6 3.6.6.6 0 1 .4 1 1V20c0 .6-.4 1-1 1A17 17 0 013 4c0-.6.4-1 1-1h3.5c.6 0 1 .4 1 1 0 1.3.2 2.5.6 3.6.1.3 0 .7-.2 1z"/></svg>
    <div><small>Get a quick quote by phone</small><strong>(555) 010-2040</strong></div>
  </div>
</header>

<section class="hero">
  <div class="hero-photo" role="img" aria-label="Business people in suits holding black umbrellas and orange folders"></div>
  <div class="hero-nav prev"><svg width="12" height="18" viewBox="0 0 12 18"><path d="M10 2L3 9l7 7" stroke="#333" stroke-width="3" fill="none"/></svg></div>
  <div class="hero-nav next"><svg width="12" height="18" viewBox="0 0 12 18"><path d="M2 2l7 7-7 7" stroke="#333" stroke-width="3" fill="none"/></svg></div>
  <div class="hero-copy">
    <h1 class="hero-title">Business Insurance</h1>
    <a class="btn">Get a Quote!</a>
  </div>
</section>

<section class="lines">
  <article class="line-card">
    <div class="line-icon"><svg width="50" height="50" viewBox="0 0 50 50" fill="#fff"><rect x="8" y="18" width="20" height="18"/><rect x="12" y="10" width="12" height="10" fill="none" stroke="#fff" stroke-width="3"/><rect x="30" y="6" width="4" height="32"/><rect x="34" y="34" width="12" height="4"/><circle cx="13" cy="40" r="5"/><circle cx="27" cy="40" r="5"/></svg></div>
    <h3>Lift</h3>
    <p>Simple cover for your family, built around your plans and your budget today.</p>
    <a class="btn">Get a Quote</a>
  </article>
  <article class="line-card">
    <div class="line-icon"><svg width="54" height="50" viewBox="0 0 54 50" fill="#fff"><path d="M10 22l6-12h22l6 12h4v14H6V22z"/><rect x="19" y="13" width="16" height="8" fill="#1f5fa8"/><circle cx="15" cy="29" r="3" fill="#1f5fa8"/><circle cx="39" cy="29" r="3" fill="#1f5fa8"/><rect x="9" y="36" width="8" height="6"/><rect x="37" y="36" width="8" height="6"/></svg></div>
    <h3>Auto</h3>
    <p>Protect every drive with flexible plans, fair rates and quick claim help.</p>
    <a class="btn">Get a Quote</a>
  </article>
  <article class="line-card">
    <div class="line-icon"><svg width="50" height="50" viewBox="0 0 50 50" fill="#fff"><path d="M25 6L4 24h6v20h11V32h8v12h11V24h6z"/></svg></div>
    <h3>Home</h3>
    <p>Keep your house and belongings safe with cover that fits the way you live.</p>
    <a class="btn">Get a Quote</a>
  </article>
  <article class="line-card">
    <div class="line-icon"><svg width="50" height="50" viewBox="0 0 50 50" fill="#fff"><path d="M18 12V8h14v4h12v28H6V12zm4 0h6V11h-6z"/><rect x="6" y="24" width="38" height="3" fill="#1f5fa8"/></svg></div>
    <h3>Business</h3>
    <p>Coverage for owners and teams so your company can keep moving ahead.</p>
    <a class="btn">Get a Quote</a>
  </article>
</section>

<section class="quote">
  <aside class="agent">
    <div class="agent-photo" role="img" aria-label="Portrait photo of the agent"></div>
    <h4>Owen Harlow - Agent</h4>
    <div class="tel"><svg width="20" height="20" viewBox="0 0 24 24"><circle cx="12" cy="12" r="12" fill="#1f5fa8"/><path fill="#fff" d="M8.5 11a8 8 0 004.5 4.5l1.4-1.4c.2-.2.4-.2.6-.1l2 .6v2.4c0 .3-.2.5-.5.5A10 10 0 016.5 7c0-.3.2-.5.5-.5h2.4l.6 2c.1.2 0 .4-.1.6z"/></svg>(555) 010-7788</div>
    <address>418 Maple Row<br>Brookfield, ST 00000</address>
  </aside>
  <form class="quote-form">
    <h2>Get An Instant <span>Insurance Quote.</span></h2>
    <div class="fields">
      <div class="field"><label>First Name:</label><div class="input"></div></div>
      <div class="field"><label>Height/Weight:</label><div class="input"></div></div>
      <div class="field"><label>Sex:</label><div class="input">Select</div></div>
      <div class="field"><label>Tobacco Use:</label><div class="input">Select</div></div>
      <div class="field"><label>Date of Birth:</label><div class="triple"><div class="input">Month</div><div class="input">Day</div><div class="input">Year</div></div></div>
      <div class="field"><label>Phone:</label><div class="input"></div></div>
      <div class="field"><label>Current Health:</label><div class="input">Select</div></div>
      <div class="field"><label>Email:</label><div class="input"></div></div>
    </div>
    <button class="btn" type="button">Submit</button>
  </form>
</section>

<section class="about">
  <h2 class="section-title">About <span>Insurance Agent</span></h2>
  <p>We are a local insurance office that helps families and business owners compare plans from many trusted carriers. Our agents listen first, explain each option in plain words and find the cover that suits your needs and budget. From your first quote to your next claim, we stay close and ready to help whenever questions come up along the way.</p>
</section>

<section class="reviews">
  <div class="reviews-head">
    <svg width="14" height="20" viewBox="0 0 12 18"><path d="M10 2L3 9l7 7" stroke="#333" stroke-width="3" fill="none"/></svg>
    <h2 class="section-title">Our Customer <span>Review</span></h2>
    <svg width="14" height="20" viewBox="0 0 12 18"><path d="M2 2l7 7-7 7" stroke="#333" stroke-width="3" fill="none"/></svg>
  </div>
  <div class="reviews-list">
    <div class="review">
      <p class="bubble">“The agent walked me through every option and found a plan that saved our family money. Getting a quote took only a few minutes and the follow up was friendly, clear and fast. I would happily recommend this office to friends and neighbors.”</p>
      <div class="who"><div class="pic" role="img" aria-label="Customer photo"></div><span>Mr Ellis Varden</span></div>
    </div>
    <div class="review">
      <p class="bubble">“Switching my business cover was easy. They answered every question, compared several carriers and kept me updated the whole time. Great service from start to finish and a fair price that fits our small company budget well.”</p>
      <div class="who"><div class="pic" role="img" aria-label="Customer photo"></div><span>Mr Ellis Varden</span></div>
    </div>
  </div>
</section>

<section class="partners">
  <h2 class="section-title">Insurance <span>Company</span></h2>
  <div class="partner-row">
    <svg width="14" height="20" viewBox="0 0 12 18"><path d="M10 2L3 9l7 7" stroke="#1f5fa8" stroke-width="3" fill="none"/></svg>
    <div class="partner"><i></i>Ledgerly</div>
    <div class="partner"><i></i>Fieldnote</div>
    <div class="partner"><i></i>Norvane</div>
    <div class="partner"><i></i>Beamwork</div>
    <div class="partner"><i></i>Stagepoint</div>
    <svg width="14" height="20" viewBox="0 0 12 18"><path d="M2 2l7 7-7 7" stroke="#1f5fa8" stroke-width="3" fill="none"/></svg>
  </div>
</section>

<section class="disclaimer">
  <h5>Disclaimer</h5>
  <p>Quotes shown are estimates only and may change after review of your details. Coverage is subject to the terms, limits and exclusions of each policy. Not all products are offered in every state. Please speak with a licensed agent before you make a final decision about your insurance.</p>
</section>

<footer class="site-footer">
  <span>© 2015 Insurance Agent. All Rights Reserved.</span>
  <span class="brand">Insurance Agent</span>
</footer>

</body>
</html>
```